Brintel Wireless generic phone package design

Hello, We are a new wireless carrier and we need a simple but impressive looking design for our generic Brintel Wireless phone box. I have included a box design idea we've been playing with, just to show the simplicity of it. Dimension of the box should 4.5x7.5x2 inches. We do have a website if you'd like to look at our company, attached a few pictures, our Logo and a the wallpaper we like to use. Our slogan is " Now I Can REALLY Hear You!" that we'd like to have on the box, the logo as well and our website address "brintelwireless.example". Just a few things to mention that are important in the design. Of course if you have great vision and would like to provide us with a great design completely different from what we've envisioned would love to see it as well.
Orr website is www.brintelwireless.example, please feel free to visit the site for some ideas. Thank you

Reason: I wanted to extend current deadline due to limited response so far. I can have the project due date extended til Nov 5th , I also need to make dessision by then. I'd like to get a few more ideas before picking the perfect design for our soft launch. Thank you

Industry/Entity Type

Telecommunications

Font styles to use
Serif

Requirements
Must have
• Logo
• brintelwireless.example
• Now I Can REALLY Hear You!
Should not have
• Address or phone number

```html
<!DOCTYPE html>
<html lang="en">
<head>
<meta charset="utf-8">
<title>Brintel Wireless – Phone Box Design</title>
<link rel="stylesheet" href="https://fonts.googleapis.com/css2?family=Alfa+Slab+One&display=swap">
<style>
  :root {
    --stage: #8c8c8c;
    --box-black: #121212;
    --box-black-soft: #1c1c1c;
    --red: #e0262b;
    --red-light: #f03a3c;
    --red-dark: #a8161c;
    --stripe: #9c1a1f;
    --ink: #111111;
    --white: #ffffff;
    --logo-grey: #d9d9d9;
  }
  * { margin: 0; padding: 0; box-sizing: border-box; }
  html, body {
    width: 907px;
    height: 1200px;
    overflow: hidden;
    background: var(--stage);
  }
  .canvas {
    position: relative;
    width: 907px;
    height: 1200px;
  }
  .panel {
    position: absolute;
    left: 152px;
    width: 600px;
    background: radial-gradient(ellipse at 70% 50%, var(--box-black-soft), var(--box-black) 70%);
    overflow: hidden;
    box-shadow: 0 4px 14px rgba(0,0,0,.45);
  }
  .panel--lid { top: 530px; height: 370px; }
  .panel--side { top: 920px; height: 182px; }

  .red-band {
    position: absolute;
    left: 84px;
    top: 0;
    width: 282px;
    height: 100%;
    background: radial-gradient(ellipse at 55% 60%, var(--red-light), var(--red) 45%, var(--red-dark) 100%);
  }
  .circuit-tree {
    position: absolute;
    left: 2px;
    top: 6px;
    width: 160px;
    height: 364px;
    background: linear-gradient(180deg, rgba(120,14,18,.55), rgba(150,20,24,.35) 60%, rgba(120,14,18,.5));
    border-radius: 6px;
  }
  .slogan {
    position: absolute;
    right: 10px;
    top: 165px;
    font-family: "Alfa Slab One", Georgia, serif;
    text-align: right;
    color: var(--ink);
    line-height: 1;
  }
  .slogan__line { display: block; font-size: 24px; }
  .slogan__line--big { font-size: 42px; color: var(--white); margin: 4px 0 2px; }
  .slogan__line--last { font-size: 32px; }

  .brand {
    position: absolute;
    right: 14px;
    top: 330px;
    font-family: "Alfa Slab One", Georgia, serif;
    font-size: 8px;
    color: var(--logo-grey);
    display: flex;
    align-items: center;
    gap: 4px;
  }
  .brand__mark {
    width: 9px; height: 9px;
    border-radius: 50%;
    background: var(--logo-grey);
  }
  .phone-art {
    position: absolute;
    left: 372px;
    top: 220px;
    width: 210px;
    height: 110px;
  }
  .stripes { position: absolute; inset: 0; }
</style>
</head>
<body>
<main class="canvas">

  <section class="panel panel--lid" aria-label="Box lid">
    <div class="red-band">
      <div class="circuit-tree" role="img" aria-label="Circuit tree illustration with app icons"></div>
      <p class="slogan">
        <span class="slogan__line">Now I Can</span>
        <span class="slogan__line slogan__line--big">REALLY</span>
        <span class="slogan__line slogan__line--last">Hear You!</span>
      </p>
      <p class="brand"><span class="brand__mark"></span>brintelwireless.example</p>
    </div>
    <svg class="phone-art" viewBox="0 0 210 110" role="img" aria-label="Smartphone illustration">
      <polygon points="8,66 168,4 204,38 44,104" fill="#0d0d0d" stroke="#c8262b" stroke-width="2"/>
    </svg>
  </section>

  <section class="panel panel--side" aria-label="Box side">
    <div class="red-band">
      <svg class="stripes" viewBox="0 0 282 182" preserveAspectRatio="none" aria-hidden="true">
        <rect x="38" y="0" width="42" height="182" fill="var(--stripe)"/>
        <rect x="108" y="0" width="14" height="182" fill="var(--stripe)"/>
        <rect x="170" y="0" width="18" height="182" fill="var(--stripe)"/>
        <rect x="246" y="0" width="10" height="182" fill="var(--stripe)"/>
      </svg>
    </div>
  </section>

</main>
</body>
</html>
```